WordPress Design (redesign) and Coding for Funeral Consulting Services & mobile app

I need an attractive SEO friendly WordPress design.

Incorporating all of the latest design standards in a graceful and appealing way. I'd like to see CTA's for for funeral consulting services. People should be able to purchase my consulting services directly from the website so I'd like to see nice buttons.

Funeral Consulting Services are the main topic for this website.

I also have an iOS app called Velomarque in the iOS Appvault Shelf. I want buttons and CTAs so that users can download the app right to their iOS device(s). Make this a secondary focus.

I want more of a mobile focus as that is where I expect the most traffic. Mobile users like to act quickly and they also like to scroll if their interest is captured so I want the design to reflect that.

End to end design
Large Creative Typography for increased mobile searchers.
attractive CTA’s
RGB Vivid / Bright Colors that match our logo
A menu that is easy to find and use on mobile devices
button(s) for iOS app download.

the current website is www.velomarque-example.com This website was a placeholder.
Updates

I'd need users to fill out a survey so that I may collect information from them to better provide service to them.

reference websites: Quillvant.com & Torbex.com for website design inspiratioin. reference Harnwick.com for blog

Target Market(s)

18-35 year old mobile users

Industry/Entity Type

Consulting

Coding

Coded - Design and coding required

Font styles to use
Sans Serif

Colors
fbee3d
000000
ffffff
cbcbcb
fefdec

Requirements
Must have
• iOS app logo and iOS app logo colors should have its own area/page
• CTA's for consulting services and app download. Main topic
• reviews (testimonials)
• Video area
• end to end design
• creative typography
Nice to have
• a beautiful blog page that blends well with the design
Should not have
• Any imagery related to funerals or burials.

```html
<!DOCTYPE html>
<html lang="en">
<head>
<meta charset="utf-8">
<title>Velomarque – Funeral Consulting Services</title>
<link href="https://fonts.googleapis.com/css2?family=Lato:wght@400;700&family=Lora:wght@400;700&display=swap" rel="stylesheet">
<style>
:root{
  --yellow:#fbee3d;
  --black:#000000;
  --white:#ffffff;
  --grey:#cbcbcb;
  --cream:#fefdec;
  --ink:#222222;
  --text:#333333;
  --muted:#666666;
  --section-grey:#ececec;
  --band-dark:#2a2a2a;
  --gold:#b8923a;
  --footer:#e4e4e4;
}
*{box-sizing:border-box;margin:0;padding:0}
html,body{width:1200px;height:4091px;overflow:hidden;background:var(--white)}
body{font-family:'Lato',sans-serif;color:var(--text);position:relative}
.section{position:absolute;left:0;width:1200px;overflow:hidden}
.abs{position:absolute}
.heading{font-family:'Lora',serif;font-weight:400;font-size:40px;color:var(--ink);text-align:center;width:100%}
.divider{left:480px;width:240px;height:10px}
.body-text{font-size:15.5px;line-height:19.5px;color:var(--text);text-align:justify}
.body-text p+p{margin-top:6px}
.btn{display:inline-flex;align-items:center;justify-content:center;height:48px;padding:0 18px;background:var(--yellow);color:var(--ink);font-family:'Lora',serif;font-size:17px;border-radius:2px;text-decoration:none}
.photo{border-radius:1px}
/* header */
.site-header{top:0;height:125px;background:var(--white)}
.brand{left:131px;top:34px;font-family:'Lora',serif;font-weight:700;font-size:38px;color:var(--black);display:flex;align-items:center;gap:10px}
.brand-dot{width:14px;height:14px;background:var(--yellow);border-radius:50%}
.phone{right:134px;top:28px;font-family:'Lora',serif;font-size:24px;color:var(--ink);display:flex;align-items:center;gap:10px}
.main-nav{right:134px;top:84px;display:flex;gap:30px;font-family:'Lora',serif;font-size:14px;color:#444}
.main-nav a{color:inherit;text-decoration:none}
.main-nav .active{color:var(--black);border-bottom:1px solid var(--black);padding-bottom:3px}
/* hero */
.hero{top:125px;height:491px;background:linear-gradient(100deg,#a8773d 0%,#d9b279 22%,#f3e6cf 45%,#efe2cf 60%,#b89c86 80%,#6e5c5a 100%)}
.hero-title{top:184px;width:100%;text-align:center;font-family:'Lora',serif;font-weight:700;font-size:44px;color:#2b2620}
.hero-cta{left:529px;top:246px;width:142px;height:50px}
.arrow{width:30px;height:30px}
/* welcome */
.welcome{top:616px;height:497px;background:var(--white)}
/* grey blocks */
.grey{background:var(--section-grey)}
/* dark bands */
.band{background:linear-gradient(135deg,#3a3a3a,#1c1c1c 60%,#2e2e2e)}
.band-text{left:160px;width:880px;text-align:center;font-family:'Lora',serif;font-size:20px;line-height:30px;color:var(--white)}
/* app */
.app-icon{left:131px;width:117px;height:117px;background:var(--black);border-radius:18px}
.app-name{left:267px;font-family:'Lora',serif;font-weight:700;font-size:30px;color:var(--black)}
/* blog */
.card{width:298px}
.card-title{font-size:14px;line-height:18px;color:var(--ink);margin-top:22px}
.card-date{font-size:11px;color:var(--muted);margin-top:10px}
/* reviews */
.reviews{top:3641px;height:354px;background:linear-gradient(135deg,#2e2e2e,#151515 55%,#2a2a2a)}
.review-text{left:150px;width:900px;top:136px;text-align:center;font-family:'Lora',serif;font-size:19.5px;line-height:36px;color:#eeeeee}
.review-name{top:258px;width:100%;text-align:center;font-family:'Lora',serif;font-size:19px;line-height:24px;color:var(--yellow)}
/* footer */
.site-footer{top:3995px;height:96px;background:var(--footer)}
.footer-links{left:131px;top:30px;font-size:12px;color:#555;display:flex;gap:8px}
.footer-copy{left:131px;top:56px;font-size:12px;color:#555}
.social{right:134px;top:36px;display:flex;gap:26px}
.social span{width:18px;height:18px;border-radius:50%;background:#555;display:block}
</style>
</head>
<body>

<header class="section site-header">
  <div class="abs brand"><span class="brand-dot"></span>Velomarque</div>
  <div class="abs phone">
    <svg width="16" height="24" viewBox="0 0 16 24" aria-hidden="true"><rect x="1" y="1" width="14" height="22" rx="2" fill="none" stroke="#222" stroke-width="2"/><rect x="6" y="18" width="4" height="2" fill="#222"/></svg>
    456 555 0148
  </div>
  <nav class="abs main-nav">
    <a class="active" href="#">Home</a><a href="#">About Us</a><a href="#">Services</a><a href="#">Testimonials</a><a href="#">Contact Us</a>
  </nav>
</header>

<section class="section hero" role="img" aria-label="Sunlit golden grass field at sunset">
  <h1 class="abs hero-title">Funeral Consulting Services</h1>
  <a class="abs btn hero-cta" href="#">Contact Us</a>
  <svg class="abs arrow" style="left:44px;top:230px" viewBox="0 0 30 30" aria-hidden="true"><circle cx="15" cy="15" r="14" fill="rgba(0,0,0,.35)"/><path d="M18 9l-6 6 6 6" stroke="#fff" stroke-width="2.5" fill="none"/></svg>
  <svg class="abs arrow" style="left:1126px;top:230px" viewBox="0 0 30 30" aria-hidden="true"><circle cx="15" cy="15" r="14" fill="rgba(0,0,0,.35)"/><path d="M12 9l6 6-6 6" stroke="#fff" stroke-width="2.5" fill="none"/></svg>
</section>

<section class="section welcome">
  <h2 class="abs heading" style="top:72px">Welcome</h2>
  <svg class="abs divider" style="top:129px" viewBox="0 0 240 10" aria-hidden="true"><line x1="0" y1="5" x2="240" y2="5" stroke="#b8923a" stroke-width="2"/><line x1="90" y1="5" x2="150" y2="5" stroke="#333" stroke-width="3"/></svg>
  <div class="abs body-text" style="left:131px;top:175px;width:440px">
    <p>Funerals are expensive. Having to finance one suddenly can be a burden to many families, especially those that are uninsured or unprepared. Not coincidently, there is often a windfall of money at this time, in the form of donations, family contributions, and life insurance proceeds. Families tend to consider that money ‘going away’ funds. The funeral industry wants to pressure you into spending your last dollar on that event</p>
  </div>
  <a class="abs btn" style="left:131px;top:367px;width:288px" href="#">DON'T Throw Money Away</a>
  <div class="abs photo" style="left:627px;top:178px;width:439px;height:240px;background:linear-gradient(120deg,#c9cfd8,#8c97a8 45%,#5a6478 75%,#cfd3da)" role="img" aria-label="Consultant meeting with a couple at a desk"></div>
</section>

<section class="section grey" style="top:1113px;height:401px">
  <div class="abs photo" style="left:131px;top:79px;width:439px;height:242px;background:linear-gradient(110deg,#8b7a68,#c9bcaa 40%,#e4ddd3 65%,#6e6259)" role="img" aria-label="Family talking with a consultant in a bright living room"></div>
  <div class="abs body-text" style="left:622px;top:114px;width:444px">
    <p>A funeral consultant is someone who, on their own, goes out and does all the things related to making funeral arrangements. However we do so with your budget and your ideals in mind. We represent you as your spokesperson and friend during this tough time.</p>
  </div>
  <a class="abs btn" style="left:620px;top:233px;width:176px" href="#">Get Help ASAP</a>
</section>

<section class="section band" style="top:1514px;height:294px" role="img" aria-label="Dark background with soft flower silhouettes">
  <p class="abs band-text" style="top:84px">The fact is, life insurance was never intended to be fully used on a fancy funeral, but rather as a hedge against disaster for the survivors.</p>
  <a class="abs btn" style="left:489px;top:165px;width:222px" href="#">SAVE MONEY NOW</a>
</section>

<section class="section" style="top:1808px;height:581px;background:var(--white)">
  <h2 class="abs heading" style="top:74px">Our App</h2>
  <svg class="abs divider" style="top:131px" viewBox="0 0 240 10" aria-hidden="true"><line x1="0" y1="5" x2="240" y2="5" stroke="#b8923a" stroke-width="2"/><line x1="90" y1="5" x2="150" y2="5" stroke="#333" stroke-width="3"/></svg>
  <div class="abs body-text" style="left:131px;top:196px;width:447px">
    <p>Aliquam erat volutpat. Quisque aliquet ex nec est vestibulum pulvinar. Pellentesque convallis molestie enim sit amet efficitur. Etiam id imperdiet lectus. Vivamus lacus justo, ultrices nec erat in, euismod iaculis mauris. Vivamus eleifend vitae nulla vel malesuada. In ac malesuada lacus, et consectetur ante. Fusce vitae lectus sit amet mi pulvinar maximus. Aenean placerat, nibh vel.</p>
  </div>
  <div class="abs app-icon" style="top:382px"></div>
  <div class="abs app-name" style="top:388px">Velomarque</div>
  <a class="abs btn" style="left:267px;top:450px;width:178px" href="#">Download Now</a>
  <div class="abs photo" style="left:627px;top:194px;width:439px;height:305px;background:linear-gradient(160deg,#e9e6ee,#b9b3c6 45%,#55506a 100%)" role="img" aria-label="App tribute video preview">
    <svg class="abs" style="left:184px;top:117px" width="70" height="70" viewBox="0 0 70 70" aria-hidden="true"><rect width="70" height="60" y="5" rx="6" fill="#3a7bc0" opacity=".9"/><path d="M27 22l20 13-20 13z" fill="#fff"/></svg>
  </div>
</section>

<section class="section grey" style="top:2389px;height:461px">
  <div class="abs photo" style="left:131px;top:79px;width:439px;height:303px;background:linear-gradient(115deg,#4a4a4a,#9a9a9a 40%,#c9c3bb 60%,#3c3c3c)" role="img" aria-label="Young couple reviewing papers on a sofa"></div>
  <div class="abs body-text" style="left:622px;top:79px;width:444px">
    <p>The first step in funeral planning, particularly if you find yourself at-need, is to get a friend by your side. This should be someone who is somewhat removed from the deceased, so the friend’s emotions will not be a factor. It should also be someone whose judgement you trust and, preferably, someone who has been through the arrangement process in the recent past.</p>
    <p>This friend should be someone who has the strength of character to say ‘NO’ or at least ‘Not YET’, to keep you from being pressured into hasty, expensive financial decisions.</p>
  </div>
  <a class="abs btn" style="left:620px;top:331px;width:214px" href="#">Save Money Today</a>
</section>

<section class="section" style="top:2850px;height:294px;background:linear-gradient(180deg,#1e1e1e,#2f2f2f 50%,#1a1a1a)" role="img" aria-label="Dark textured background">
  <p class="abs band-text" style="top:87px">In a survey of several thousand funeral directors, in response to the question Why would you say funerals cost so much?, over 85% replied “Emotional overspending by the family.”</p>
  <a class="abs btn" style="left:521px;top:162px;width:158px" href="#">Get help now</a>
</section>

<section class="section" style="top:3144px;height:497px;background:var(--white)">
  <h2 class="abs heading" style="top:75px">Blog</h2>
  <svg class="abs divider" style="top:132px" viewBox="0 0 240 10" aria-hidden="true"><line x1="0" y1="5" x2="240" y2="5" stroke="#b8923a" stroke-width="2"/><line x1="90" y1="5" x2="150" y2="5" stroke="#333" stroke-width="3"/></svg>
  <article class="abs card" style="left:131px;top:178px">
    <div class="photo" style="height:163px;background:linear-gradient(180deg,#cfe0ee,#e9e2d2 55%,#b59a72)" role="img" aria-label="Couple walking on a beach"></div>
    <h3 class="card-title" style="font-weight:400">Pellentesque pulvinar posuere velit et. Curabitur sollicitudin efficitur egestas</h3>
    <p class="card-date">28 Dec, 2017</p>
  </article>
  <article class="abs card" style="left:451px;top:178px">
    <div class="photo" style="height:163px;background:linear-gradient(135deg,#7a5a4a,#d8b9a2 45%,#efe2d4 70%,#8d6b58)" role="img" aria-label="Two hands holding each other"></div>
    <h3 class="card-title" style="font-weight:400">Etiam mattis augue vehicula odio posuere, sit amet tempus lectus luctus</h3>
    <p class="card-date">28 Dec, 2017</p>
  </article>
  <article class="abs card" style="left:768px;top:178px">
    <div class="photo" style="height:163px;background:linear-gradient(160deg,#f0d79a,#d8b06a 40%,#a88a66 70%,#e8e0cf)" role="img" aria-label="Group of smiling older friends outdoors"></div>
    <h3 class="card-title" style="font-weight:400">Etiam vel massa elementum, bibendum tellus venenatis, feugiat massa</h3>
    <p class="card-date">28 Dec, 2017</p>
  </article>
</section>

<section class="section reviews" role="img" aria-label="Dark textured background">
  <h2 class="abs heading" style="top:68px;color:var(--white)">App Reviews</h2>
  <p class="abs review-text">Proin a dolor mauris. Vestibulum ante ipsum primis in faucibus orci luctus et ultrices posuere cubilia Curae; Vestibulum eget nisi metus. Phasellus nisi est, condimentum vitae faucibus in, sollicitudin vel metus. Nunc sit amet consequat risus. Curabitur ac elit leo.</p>
  <p class="abs review-name">Marten Vale, City</p>
  <svg class="abs" style="left:50px;top:163px" width="16" height="22" viewBox="0 0 16 22" aria-hidden="true"><path d="M12 3l-8 8 8 8" stroke="#fff" stroke-width="3" fill="none"/></svg>
  <svg class="abs" style="left:1134px;top:163px" width="16" height="22" viewBox="0 0 16 22" aria-hidden="true"><path d="M4 3l8 8-8 8" stroke="#fff" stroke-width="3" fill="none"/></svg>
</section>

<footer class="section site-footer">
  <nav class="abs footer-links"><span>Home</span><span>|</span><span>About Us</span><span>|</span><span>Services</span><span>|</span><span>Testimonials</span><span>|</span><span>Contact Us</span></nav>
  <p class="abs footer-copy">Copyright © 2017 Velomarque . All rights reserved.</p>
  <div class="abs social" aria-label="Social links"><span></span><span></span><span></span><span></span></div>
</footer>

</body>
</html>
```